Business card for my new company (Accounting firm)

I need a business card for my new business Brightwell Advisory and Ledger SA. Our services are accounting, tax, audit and financial management. Our customers are small companies, start-ups and new companies. The final design has to show financial security, trust and growth. Please find our logo attached to the business card. Text for the business card: Brightwell Advisory and Ledger SA Tomas Varenholt Director and Founder Certified Accountant Tel. 022 418 57 34 tv@clairevalconseil.ch www.clairevalconseil.ch Rue des Vergières 27 1201 Geneva
Target Market(s)
Our customers are small companies, start-ups and new companies.
Industry/Entity Type
Finance And Accounting
Contact Information for Business Card
Claireval Conseil et Comptes SA
Tomas Varenholt
Directeur et Fondateur
Expert-comptable diplômé
Tél. 022 418 57 34
tv@clairevalconseil.ch
www.clairevalconseil.ch
Rue des Vergières 27
1201 Genève

```html
<!DOCTYPE html>
<html lang="fr">
<head>
<meta charset="utf-8">
<title>Claireval Conseil et Comptes SA – Carte de visite</title>
<link rel="stylesheet" href="https://fonts.googleapis.com/css2?family=Roboto:wght@400;500;700&family=Montserrat:wght@500&display=swap">
<style>
  :root {
    --page-bg: #d9d6d1;
    --card-bg: #efedea;
    --name-blue: #1d5f89;
    --brand-blue: #2a7fb0;
    --text-dark: #3b3b3b;
    --icon-blue: #1f5e86;
    --band-start: #14618a;
    --band-end: #2d8fb5;
    --strip-dark: #3a3a3c;
    --band-text: #d8e6ee;
  }
  * { margin: 0; padding: 0; box-sizing: border-box; }
  html, body {
    width: 1200px; height: 1054px; overflow: hidden;
    background: var(--page-bg);
  }
  .card {
    position: absolute; left: 100px; top: 225px;
    width: 1000px; height: 603px;
    background: var(--card-bg);
    overflow: hidden;
    box-shadow: 0 6px 24px rgba(0,0,0,.12);
    font-family: "Roboto", Arial, sans-serif;
  }
  .brand {
    position: absolute; left: 60px; top: 190px; width: 360px;
    display: flex; align-items: center; gap: 18px;
  }
  .brand-dot {
    flex: none; width: 46px; height: 46px; border-radius: 50%;
    background: var(--brand-blue);
  }
  .brand-name {
    font-family: "Montserrat", Arial, sans-serif; font-weight: 500;
    font-size: 30px; line-height: 1.2; letter-spacing: 1px;
    color: var(--brand-blue); text-transform: uppercase;
  }
  .person { position: absolute; left: 523px; top: 136px; }
  .person-name {
    font-weight: 700; font-size: 38px; color: var(--name-blue); line-height: 1.1;
  }
  .person-role {
    margin-top: 12px; font-size: 23px; line-height: 31px; color: var(--text-dark);
  }
  .contacts {
    position: absolute; left: 532px; top: 312px; list-style: none;
    font-size: 25px; color: var(--text-dark);
  }
  .contacts li { display: flex; align-items: center; height: 38px; }
  .contacts svg { width: 22px; height: 22px; margin-right: 18px; fill: var(--icon-blue); }
  .bottom-strip {
    position: absolute; left: 0; bottom: 0; width: 460px; height: 22px;
    background: var(--strip-dark);
  }
  .address-band {
    position: absolute; right: 0; bottom: 0; width: 580px; height: 72px;
    background: linear-gradient(90deg, var(--band-start), var(--band-end));
    clip-path: polygon(40px 0, 100% 0, 100% 100%, 0 100%);
  }
  .address {
    position: absolute; left: 523px; bottom: 20px;
    font-size: 24px; color: var(--band-text);
  }
</style>
</head>
<body>
  <div class="card">
    <div class="brand">
      <span class="brand-dot"></span>
      <span class="brand-name">Claireval<br>Conseil et Comptes</span>
    </div>

    <div class="person">
      <h1 class="person-name">Tomas Varenholt</h1>
      <p class="person-role">Directeur et Fondateur<br>Expert-comptable diplômé</p>
    </div>

    <ul class="contacts">
      <li>
        <svg viewBox="0 0 24 24" aria-hidden="true"><path d="M3 8c0-3 4-5 9-5s9 2 9 5v2h-5V8c-2-1-6-1-8 0v2H3zM6 12h12l3 8H3z"/></svg>
        022 418 57 34
      </li>
      <li>
        <svg viewBox="0 0 24 24" aria-hidden="true"><path d="M2 5h20v14H2zM3 6l9 7 9-7" stroke="#efedea" stroke-width="1.6"/></svg>
        tv@clairevalconseil.ch
      </li>
      <li>
        <svg viewBox="0 0 24 24" aria-hidden="true"><circle cx="12" cy="12" r="10"/><path d="M2 12h20M12 2c-4 4-4 16 0 20M12 2c4 4 4 16 0 20" fill="none" stroke="#efedea" stroke-width="1.4"/></svg>
        www.clairevalconseil.ch
      </li>
    </ul>

    <div class="bottom-strip"></div>
    <div class="address-band"></div>
    <p class="address">Rue des Vergières 27 1201 Genève</p>
  </div>
</body>
</html>
```